Bright Net Rally Website Design (design layout only)

We need a website design for a new nonprofit organization based in Des Moines, Iowa called Bright Net Rally. The nonprofit provides soccer training opportunities to youth soccer players looking to improve their game while also affecting the lives of the less fortunate in a positive way. While participating in the training programs the players also go out and raise money for selected charities. The organization then donates the funds. In its first 18 months we donated $10,500. We would like to see designs attempt to symbolize the mission of the nonprofit - essentially "improve you while improving someone else."

We would like to see the following features:

· A place to donate - Our intent is to have the home page linked to the donation page; a simple straight-forward process for people to give money, and make donating as painless as possible - no account needed to make a donation, credit card or e-check should be the only information needed to donate, and have it be on a single page.

· A photo gallery so people can browse the photo gallery to get a better understanding of our organization and a place to add videos and a calendar to show upcoming events

· A place for contact information and the profiles of directors and board members. This should include a spot showing all the charities the organization donates to. Also includes a news section/blog for comments and suggestions.

We want the design to revolve around the content and mission. We would really like to stress our organization as nonprofit. We would also like if the website was user friendly and easy to navigate.

The logo of our organization is uploaded

```html
<!DOCTYPE html>
<html lang="en">
<head>
<meta charset="utf-8">
<title>Bright Net Rally</title>
<link href="https://fonts.googleapis.com/css2?family=Roboto:wght@300;400;500;700;900&family=Roboto+Condensed:wght@700&display=swap" rel="stylesheet">
<style>
:root{
  --green:#7a9a48;
  --green-bright:#6cae2e;
  --green-dark:#4a6a33;
  --ink:#333;
  --page:#f1f1f2;
  --page-band:#e7e7e8;
  --white:#fff;
  --line:#d9d9d9;
  --navy:#3b5998;
  --slate:#5a6f9c;
  --hero:#5d7358;
}
*{box-sizing:border-box;margin:0;padding:0}
html,body{width:713px;height:1200px;overflow:hidden;background:var(--page)}
body{font-family:"Roboto",Arial,sans-serif;color:var(--ink)}
.canvas{position:relative;width:713px;height:1200px;overflow:hidden;background:var(--page)}
.abs{position:absolute}

/* hero backdrop */
.hero-backdrop{left:0;top:66px;width:713px;height:254px;background:var(--hero)}
.band{left:0;top:320px;width:713px;height:232px;background:var(--page-band)}
.header-sky{left:0;top:0;width:713px;height:66px;background:#e9ecef}

/* header */
.brand{left:103px;top:10px;display:flex;align-items:center;gap:8px}
.brand-mark{width:38px;height:38px;background:var(--green)}
.brand-name{font-family:"Roboto Condensed","Roboto",sans-serif;font-weight:700;font-size:23px;line-height:21px;color:var(--green);letter-spacing:.5px}
.nav{left:343px;top:27px;display:flex}
.nav a{display:block;width:54px;text-decoration:none;text-align:center;border-left:1px solid #c3c8cd;color:#3a4a55}
.nav a:first-child{border-left:0}
.nav .label{display:block;font-size:9px;line-height:11px}
.nav .sub{display:block;font-size:6px;line-height:9px;color:#666}
.nav-notch{left:352px;top:0;width:30px;height:5px;background:var(--green);clip-path:polygon(0 0,100% 0,50% 100%)}

/* slider */
.slider{left:102px;top:65px;width:510px;height:296px;background:var(--white);box-shadow:0 1px 3px rgba(0,0,0,.15)}
.slide-photo{left:6px;top:6px;width:498px;height:244px;background:linear-gradient(180deg,#3d5a2c,#62a040)}
.slide-dots{left:220px;top:243px;width:54px;height:14px;background:var(--green-dark);border-radius:7px 7px 0 0;display:flex;gap:4px;justify-content:center;align-items:center}
.slide-dots span{width:5px;height:5px;border-radius:50%;background:#cfd8c4}
.slide-dots span.on{background:var(--white)}
.slide-title{left:0;top:261px;width:510px;text-align:center;font-size:12.5px;font-weight:400;color:#333}
.slide-text{left:0;top:278px;width:510px;text-align:center;font-size:7px;color:#666}

/* donate bar */
.donate{left:102px;top:376px;width:510px;height:41px;background:var(--white);border:1px solid var(--line)}
.donate-tag{left:-1px;top:-1px;width:174px;height:41px;background:linear-gradient(180deg,#7fc63a,#4e9a1f);
  clip-path:polygon(0 0,89% 0,100% 50%,89% 100%,0 100%);color:var(--white);font-weight:700;font-size:10.5px;line-height:13px;padding:7px 0 0 14px}
.donate-label{left:191px;top:12px;font-size:12px;color:#666}
.donate-field{left:260px;top:6px;width:153px;height:27px;border:1px solid #ddd;background:#fafafa;display:flex;align-items:center;padding-left:14px;gap:8px}
.donate-field .cur{font-size:12px;color:#666}
.donate-field .amt{font-size:19px;font-weight:300;color:#444}
.btn-green{background:var(--green);color:var(--white);font-weight:700;text-align:center;border-radius:2px}
.donate-btn{left:427px;top:5px;width:78px;height:28px;line-height:28px;font-size:11px}

/* feature cards */
.card{top:425px;width:156px;height:157px;background:var(--white);box-shadow:0 6px 6px -4px rgba(0,0,0,.18)}
.card-photo{left:0;top:0;width:156px;height:70px}
.card-title{left:0;top:80px;width:156px;text-align:center;font-weight:700;font-size:11px;color:var(--green-dark)}
.card-text{left:12px;top:96px;width:132px;text-align:center;font-size:6.5px;line-height:9px;color:#777}
.card-more{left:52px;top:131px;width:52px;height:17px;line-height:15px;border:1px solid #ccc;font-size:6.5px;text-align:center;color:#444;border-radius:2px}
.campaign-title{left:0;top:82px;width:156px;text-align:center;font-weight:700;font-size:11px;color:var(--green-dark)}
.campaign-sum{left:0;top:95px;width:156px;text-align:center;font-size:13px;font-weight:500;color:var(--green)}
.campaign-donors{left:0;top:112px;width:156px;text-align:center;font-size:8px;color:#999}
.join-btn{left:44px;top:130px;width:67px;height:25px;line-height:25px;font-size:11px;border-radius:3px}

/* gallery */
.section-title{font-family:"Roboto Condensed","Roboto",sans-serif;font-weight:700;color:var(--green-dark);font-size:16px}
.gallery-title{left:103px;top:609px}
.gallery-arrow{top:616px;width:19px;height:19px;background:#3a3a3a;display:flex;align-items:center;justify-content:center}
.gallery-strip{left:102px;top:642px;display:flex;gap:2px}
.gallery-strip div{width:100.4px;height:76px}

/* campaigns banner */
.campaign-banner{left:102px;top:735px;width:510px;height:70px;background:var(--white)}
.campaign-panel{left:10px;top:7px;width:494px;height:58px;border-radius:4px;border:1px solid #c8ced8;background:linear-gradient(180deg,#f2f4f8,#dde2ea)}
.campaign-icon{left:11px;top:6px;width:42px;height:42px;background:var(--slate);border-radius:4px;transform:rotate(45deg) scale(.78)}
.banner-title{left:66px;top:10px;font-size:18px;color:var(--slate)}
.banner-sub{left:66px;top:34px;font-size:8.5px;color:#555}
.pals-btn{left:313px;top:15px;width:168px;height:28px;background:var(--navy);border-radius:3px;display:flex;align-items:center;gap:10px;padding-left:10px;color:var(--white);font-size:12.5px}
.pals-btn i{width:12px;height:12px;background:var(--white);display:block}

/* news */
.news-title{left:104px;top:821px}
.news-item{left:103px;width:152px;height:66px;border-bottom:1px dotted #bbb}
.news-date{left:0;top:0;width:30px;height:44px;background:var(--green);color:var(--white);text-align:center}
.news-date b{display:block;font-size:15px;font-weight:700;line-height:22px;border-bottom:1px solid rgba(255,255,255,.6)}
.news-date small{display:block;font-size:7px;font-weight:700;line-height:18px}
.news-head{left:34px;top:2px;font-weight:700;font-size:8px;color:var(--green)}
.news-text{left:35px;top:14px;width:102px;font-size:6.5px;line-height:9px;color:#888}
.news-more{left:35px;top:45px;font-size:6.5px;color:var(--green)}

/* board */
.board{left:275px;top:823px;width:337px;height:244px;background:var(--green-dark)}
.board-title{left:13px;top:11px;font-weight:700;font-size:12.5px;color:var(--white)}
.profile{width:149px;height:70px;background:var(--white)}
.profile-photo{left:6px;top:6px;width:47px;height:58px}
.profile-name{left:58px;top:7px;font-weight:700;font-size:7.5px;color:var(--green)}
.profile-text{left:58px;top:19px;width:86px;font-size:6.5px;line-height:8.5px;color:#888}
.profile-more{left:60px;top:54px;font-size:6.5px;color:var(--green)}
.view-all{left:13px;top:204px;width:50px;height:17px;line-height:17px;background:var(--white);font-size:7px;text-align:center;border-radius:2px;color:#333}

/* footer */
.footer{left:0;top:1067px;width:713px;height:133px;background:var(--green-dark);color:var(--white)}
.foot-head{font-size:9.5px;font-weight:400;color:var(--white)}
.contact-row{left:103px;display:flex;gap:8px;font-size:6.5px;line-height:8.5px}
.contact-row svg{flex:none}
.copyright{left:103px;top:97px;font-size:6px}
.foot-brand{left:265px;top:30px;font-family:"Roboto Condensed","Roboto",sans-serif;font-weight:700;font-size:25px;line-height:23px;color:#6b8a52}
.social{top:92px;width:8px;height:8px;border-radius:50%;background:var(--white)}
.blog-item{left:462px;width:160px;height:30px}
.blog-thumb{left:0;top:0;width:35px;height:22px;border:1px solid var(--white)}
.blog-head{left:40px;top:0;font-weight:700;font-size:7.5px}
.blog-text{left:40px;top:10px;font-size:6.5px;line-height:8px;color:#dfe7d6}
.blog-meta{left:42px;top:27px;font-size:7px;color:#cfe09b}
</style>
</head>
<body>
<div class="canvas">

  <div class="abs hero-backdrop" role="img" aria-label="Stadium with a large soccer ball beside the pitch"></div>
  <div class="abs header-sky"></div>
  <div class="abs band"></div>

  <header>
    <div class="abs nav-notch"></div>
    <div class="abs brand">
      <span class="brand-mark"></span>
      <span class="brand-name">BRIGHT NET<br>RALLY</span>
    </div>
    <nav class="abs nav">
      <a href="#"><span class="label">Home</span><span class="sub">Who we are</span></a>
      <a href="#"><span class="label">Training</span><span class="sub">Our programs</span></a>
      <a href="#"><span class="label">Blog</span><span class="sub">more info</span></a>
      <a href="#"><span class="label">Gallery</span><span class="sub">our players</span></a>
      <a href="#"><span class="label">Contact</span><span class="sub">&amp; location</span></a>
    </nav>
  </header>

  <section class="abs slider">
    <div class="abs slide-photo" role="img" aria-label="Youth players in green kits training with balls on a grass field"></div>
    <div class="abs slide-dots"><span class="on"></span><span></span><span></span></div>
    <h2 class="abs slide-title">Aliquam ac egestas diam, vel volutpat ipsum</h2>
    <p class="abs slide-text">Quisque imperdiet volutpat magna, pretium mollis magna tempor eu. Duis malesuada, velit vitae eleifend tempus, ante eros egestas lectus,</p>
  </section>

  <section class="abs donate">
    <div class="abs donate-tag">HELP THEM TO<br>MAKE THEIR DREAMS</div>
    <span class="abs donate-label">I Will Give</span>
    <div class="abs donate-field"><span class="cur">$</span><span class="amt">1000</span></div>
    <div class="abs btn-green donate-btn">Donate Now</div>
  </section>

  <article class="abs card" style="left:102px">
    <div class="abs card-photo" role="img" aria-label="Player heading a ball against a blue sky" style="background:linear-gradient(180deg,#7fa6d6,#9fb8d0)"></div>
    <h3 class="abs card-title">FINAL TOURNAMENT</h3>
    <p class="abs card-text">Quisque imperdiet volutpat magna, pretium mollis magna tempor eu. Duis malesuada, velit vitae eleifend tempus, ante eros .</p>
    <div class="abs card-more">View more »</div>
  </article>

  <article class="abs card" style="left:279px">
    <div class="abs card-photo" role="img" aria-label="Boot on a ball on green turf" style="background:linear-gradient(180deg,#3e6a2a,#64a23c)"></div>
    <h3 class="abs card-title">COACHES</h3>
    <p class="abs card-text">Quisque imperdiet volutpat magna, pretium mollis magna tempor eu. Duis malesuada, velit vitae eleifend tempus, ante eros .</p>
    <div class="abs card-more">View more »</div>
  </article>

  <article class="abs card" style="left:456px">
    <div class="abs card-photo" role="img" aria-label="Youth team in blue kits posing with a trophy" style="background:linear-gradient(180deg,#4a6ea6,#5a7a8a)"></div>
    <h3 class="abs campaign-title">JOIN OUR CAMPAIGN!</h3>
    <div class="abs campaign-sum">$5,445</div>
    <div class="abs campaign-donors">raised by 60 donors</div>
    <div class="abs btn-green join-btn">Join Now</div>
  </article>

  <h2 class="abs section-title gallery-title">OUR GALLERY</h2>
  <div class="abs gallery-arrow" style="left:572px"><svg width="6" height="9" viewBox="0 0 6 9"><path d="M5 1 1.5 4.5 5 8" fill="none" stroke="#fff" stroke-width="1.3"/></svg></div>
  <div class="abs gallery-arrow" style="left:594px"><svg width="6" height="9" viewBox="0 0 6 9"><path d="M1 1 4.5 4.5 1 8" fill="none" stroke="#fff" stroke-width="1.3"/></svg></div>
  <div class="abs gallery-strip">
    <div role="img" aria-label="Team photo of young players with coaches" style="background:linear-gradient(180deg,#aaa99f,#85857a)"></div>
    <div role="img" aria-label="Players competing for the ball on a pitch" style="background:linear-gradient(180deg,#3f6e3a,#4f8a3a)"></div>
    <div role="img" aria-label="Championship youth team with a banner" style="background:linear-gradient(180deg,#6f8aa0,#5a72a0)"></div>
    <div role="img" aria-label="Player in red kicking a ball" style="background:linear-gradient(180deg,#3f6232,#5a8a3c)"></div>
    <div role="img" aria-label="Team in red with a trophy banner" style="background:linear-gradient(180deg,#9a7a6a,#a8443a)"></div>
  </div>

  <section class="abs campaign-banner">
    <div class="abs campaign-panel">
      <div class="abs campaign-icon"></div>
      <div class="abs banner-title">Easily Find Campaigns</div>
      <div class="abs banner-sub">See what your friends support and help spread the word!</div>
      <div class="abs pals-btn"><i></i>Backed by Pals</div>
    </div>
  </section>

  <h2 class="abs section-title news-title">LATEST NEWS</h2>

  <article class="abs news-item" style="top:850px">
    <div class="abs news-date"><b>24</b><small>JULY</small></div>
    <h4 class="abs news-head">COMPLIANCE FORMS</h4>
    <p class="abs news-text">Please fill in and return to office before Sunday 5 October 2014 (Opening Day) if you wish...</p>
    <span class="abs news-more">view more »</span>
  </article>
  <article class="abs news-item" style="top:923px">
    <div class="abs news-date"><b>22</b><small>JULY</small></div>
    <h4 class="abs news-head">COMPLIANCE FORMS</h4>
    <p class="abs news-text">Please fill in and return to office before Sunday 5 October 2014 (Opening Day) if you wish...</p>
    <span class="abs news-more">view more »</span>
  </article>
  <article class="abs news-item" style="top:998px;border-bottom:0">
    <div class="abs news-date"><b>21</b><small>JULY</small></div>
    <h4 class="abs news-head">COMPLIANCE FORMS</h4>
    <p class="abs news-text">Please fill in and return to office before Sunday 5 October 2014 (Opening Day) if you wish...</p>
    <span class="abs news-more">view more »</span>
  </article>

  <section class="abs board">
    <h2 class="abs board-title">PROFILES OF DIRECTORS AND BOARD MEMBERS</h2>
    <div class="abs profile" style="left:12px;top:41px">
      <div class="abs profile-photo" role="img" aria-label="Portrait of a board director" style="background:#7a7068"></div>
      <div class="abs profile-name">Vivamus blandit mollis</div>
      <p class="abs profile-text">Ut viverra facilisis nulla vel aliquam. Pellentesque habitant morbi tristique senectus et netus</p>
      <span class="abs profile-more">view more »</span>
    </div>
    <div class="abs profile" style="left:175px;top:41px">
      <div class="abs profile-photo" role="img" aria-label="Portrait of a board member" style="background:#8a8a8a"></div>
      <div class="abs profile-name">Vivamus blandit mollis</div>
      <p class="abs profile-text">Ut viverra facilisis nulla vel aliquam. Pellentesque habitant morbi tristique senectus et netus</p>
      <span class="abs profile-more">view more »</span>
    </div>
    <div class="abs profile" style="left:12px;top:125px">
      <div class="abs profile-photo" role="img" aria-label="Portrait of a board member" style="background:#d8cbc2"></div>
      <div class="abs profile-name">Vivamus blandit mollis</div>
      <p class="abs profile-text">Ut viverra facilisis nulla vel aliquam. Pellentesque habitant morbi tristique senectus et netus</p>
      <span class="abs profile-more">view more »</span>
    </div>
    <div class="abs profile" style="left:175px;top:125px">
      <div class="abs profile-photo" role="img" aria-label="Portrait of a board member" style="background:#a87a5e"></div>
      <div class="abs profile-name">Vivamus blandit mollis</div>
      <p class="abs profile-text">Ut viverra facilisis nulla vel aliquam. Pellentesque habitant morbi tristique senectus et netus</p>
      <span class="abs profile-more">view more »</span>
    </div>
    <div class="abs view-all">View all »</div>
  </section>

  <footer class="abs footer">
    <h3 class="abs foot-head" style="left:103px;top:14px">Contactinfo</h3>
    <div class="abs contact-row" style="top:36px">
      <svg width="9" height="9" viewBox="0 0 10 10"><path d="M5 1 0.5 5H2v4h2.5V6.5h1V9H8V5h1.5z" fill="#fff"/></svg>
      <span>345- Ut urna magna, bibendum vitae<br>ipsum at, egestas consectetur</span>
    </div>
    <div class="abs contact-row" style="top:59px">
      <svg width="9" height="9" viewBox="0 0 10 10"><path d="M2 0.8 3.6 0.6 4.4 3 3.3 3.9C3.9 5.3 4.8 6.2 6.1 6.8L7 5.6 9.4 6.4 9.2 8C9 9 8 9.4 7 9.1 4 8.2 1.8 6 0.9 3 0.6 2 1 1 2 0.8z" fill="#fff"/></svg>
      <span>(08) 4410 2273</span>
    </div>
    <div class="abs contact-row" style="top:77px">
      <svg width="9" height="9" viewBox="0 0 10 10"><rect x="0.5" y="2" width="9" height="6" fill="#fff"/><path d="M0.5 2 5 5.5 9.5 2" fill="none" stroke="#4a6a33" stroke-width="0.9"/></svg>
      <span>info@brightnetrally.org</span>
    </div>
    <p class="abs copyright">Copyright © 2014 bright net rally</p>

    <div class="abs foot-brand">BRIGHT NET<br>RALLY</div>
    <span class="abs social" style="left:323px"></span>
    <span class="abs social" style="left:347px"></span>
    <span class="abs social" style="left:373px"></span>
    <span class="abs social" style="left:400px"></span>

    <h3 class="abs foot-head" style="left:463px;top:13px">Recent Blogs</h3>
    <div class="abs blog-item" style="top:31px">
      <div class="abs blog-thumb" role="img" aria-label="Player on the pitch" style="background:#4f7a6a"></div>
      <div class="abs blog-head">Duis sapien enim,</div>
      <p class="abs blog-text">Pellentesque habitant morbi<br>tristique senectus et netus</p>
      <span class="abs blog-meta">5 comments</span>
    </div>
    <div class="abs blog-item" style="top:75px">
      <div class="abs blog-thumb" role="img" aria-label="Players training on grass" style="background:#6a9a5a"></div>
      <div class="abs blog-head">Duis sapien enim,</div>
      <p class="abs blog-text">Pellentesque habitant morbi<br>tristique senectus et netus</p>
      <span class="abs blog-meta">5 comments</span>
    </div>
  </footer>

</div>
</body>
</html>
```